New Business Card Design

We would like to refresh our business cards and make them look better. We are an IT company specialising in Cloud Services, IT Managed Services, software and hardware. I have attached a PSD of our current design. Also attached our logo.
Updates

I have uploaded all new logos in EPS format.

Can you please edit all designs to include a job title for Marcus Hollis, eg. General Manager

Industry/Entity Type

Software

Colors
ffffff

Requirements
Must have
• Please use white background.
Should not have
• Black background

```html
<!DOCTYPE html>
<html lang="en">
<head>
<meta charset="utf-8">
<title>Meridian Technology – Business Cards</title>
<link rel="stylesheet" href="https://fonts.googleapis.com/css2?family=Open+Sans:wght@400;600&display=swap">
<style>
  :root {
    --page-bg: #e4e6ea;
    --card-light: #f4f4f4;
    --card-mid: #dcdcdc;
    --ink: #2b2d30;
    --ink-soft: #4a4d52;
    --accent-red: #c8392b;
    --band-grey: #87929c;
    --divider: #b9bcc0;
  }
  * { box-sizing: border-box; margin: 0; padding: 0; }
  html, body {
    width: 1200px; height: 987px; overflow: hidden;
    background: var(--page-bg);
    font-family: "Open Sans", Arial, sans-serif;
    color: var(--ink);
  }
  .canvas {
    width: 1200px; height: 987px;
    display: flex; flex-direction: column;
    align-items: center; justify-content: center; gap: 40px;
  }
  .card {
    position: relative;
    width: 760px; height: 434px;
    border-radius: 30px;
    overflow: hidden;
    background: linear-gradient(135deg, var(--card-light) 0%, var(--card-mid) 55%, var(--card-light) 100%);
    box-shadow: 0 6px 18px rgba(0,0,0,0.14);
  }

  /* company name */
  .brand-name {
    font-weight: 600;
    color: var(--ink);
    line-height: 1.2;
  }

  /* front */
  .card-front .brand-name {
    position: absolute; left: 60px; top: 80px;
    font-size: 32px;
  }
  .contact {
    position: absolute; left: 440px; top: 140px;
    padding-left: 22px; border-left: 1px solid var(--divider);
    list-style: none;
  }
  .contact li {
    display: flex; align-items: center; gap: 10px;
    font-size: 18px; line-height: 30px; color: var(--ink);
  }
  .contact svg { width: 16px; height: 16px; flex: none; }
  .band { position: absolute; left: 0; bottom: 0; width: 760px; height: 434px; }
  .person {
    position: absolute; left: 60px; bottom: 40px; color: #fff;
  }
  .person-name { font-size: 26px; font-weight: 600; }
  .person-title { font-size: 19px; font-weight: 400; }

  /* back */
  .card-back {
    display: flex; flex-direction: column; align-items: center; justify-content: center;
    text-align: center; gap: 30px;
  }
  .card-back .brand-name { font-size: 38px; }
  .tagline { font-size: 22px; line-height: 1.4; color: var(--ink); }
  .web { font-size: 17px; letter-spacing: 0.2em; color: var(--ink-soft); }
</style>
</head>
<body>
<main class="canvas">

  <section class="card card-front" aria-label="Business card front">
    <p class="brand-name">Meridian Technology</p>

    <ul class="contact">
      <li>
        <svg viewBox="0 0 16 16" aria-hidden="true"><circle cx="8" cy="8" r="8" fill="var(--accent-red)"/><path d="M5 4.5l1.6-.6 1 2-1 .8c.4 1 1.2 1.8 2.2 2.2l.8-1 2 1-.6 1.6c-3 0-6-3-6-6z" fill="#fff"/></svg>
        07 3150 4400
      </li>
      <li>
        <svg viewBox="0 0 16 16" aria-hidden="true"><rect x="4" y="1" width="8" height="14" rx="1.5" fill="var(--accent-red)"/><rect x="5.5" y="3" width="5" height="6" fill="#fff"/></svg>
        0412 586 307
      </li>
      <li>
        <svg viewBox="0 0 16 16" aria-hidden="true"><rect x="1" y="3" width="14" height="10" rx="1.5" fill="var(--accent-red)"/><path d="M2 4.5l6 4.5 6-4.5" fill="none" stroke="#fff" stroke-width="1.3"/></svg>
        marcush@meridianit.com.au
      </li>
      <li>
        <svg viewBox="0 0 16 16" aria-hidden="true"><circle cx="8" cy="8" r="7" fill="var(--accent-red)"/><g fill="none" stroke="#fff" stroke-width="1"><ellipse cx="8" cy="8" rx="3" ry="7"/><path d="M1 8h14M2.5 4.5h11M2.5 11.5h11"/></g></svg>
        www.meridianit.com.au
      </li>
    </ul>

    <svg class="band" viewBox="0 0 760 434" aria-hidden="true">
      <path d="M0 300 Q 380 330 760 390 L 760 434 L 0 434 Z" fill="var(--band-grey)"/>
    </svg>

    <div class="person">
      <p class="person-name">Marcus Hollis</p>
      <p class="person-title">General Manager</p>
    </div>
  </section>

  <section class="card card-back" aria-label="Business card back">
    <p class="brand-name">Meridian Technology</p>
    <p class="tagline">We are an IT company specializing in Cloud Services<br>IT Managed Services, software and hardware</p>
    <p class="web">www.meridianit.com.au</p>
  </section>

</main>
</body>
</html>
```